Charity Initiative needs a WebPage design

We need a web design for charity initiative by two young guys riding their bikes around Australia to support HarbourLight which helps people with depression and anxiety. Full brief and requirements are attached in the PDF and word document. We have the logo already done and attached. Website will be done in Wordpress and need to get Donations, display current donations, show live Video feed, GPS tracker, Blogs etc and also ability to sell merchandise later

Target Market(s)

Sponsors, Business, Young People

Number of Pages Required

4 page

Font styles to use
Serif
Sans Serif
Decorative
Script

Requirements
Must have
• As per Brief and also Donation status etc
Nice to have
• Please check my logo and read the Bried

```html
<!DOCTYPE html>
<html lang="en">
<head>
<meta charset="utf-8">
<title>Ride the Rim 2016 – Riding for HarbourLight</title>
<link href="https://fonts.googleapis.com/css2?family=Oswald:wght@400;500;600&family=Open+Sans:wght@400;600;700&display=swap" rel="stylesheet">
<style>
:root{
  --pink:#e8236f;
  --cyan:#22d6ea;
  --cyan-dark:#12bfd4;
  --heading:#555555;
  --body:#6f6f6f;
  --rule:#e3e3e3;
  --band:#efefef;
  --footer:#2c2c2c;
  --footer-text:#9a9a9a;
  --green:#16b21d;
  --white:#ffffff;
}
*{margin:0;padding:0;box-sizing:border-box}
html,body{width:1200px;height:4245px;overflow:hidden}
body{position:relative;background:var(--white);font-family:"Open Sans",Arial,sans-serif;color:var(--body)}
.abs{position:absolute}

/* backdrop behind the top column */
.backdrop{left:0;top:0;width:1200px;height:863px;background:linear-gradient(180deg,#7fa8c9 0%,#c9c1a8 45%,#8e8770 100%)}
.column{left:68px;top:0;width:1064px;height:863px;background:var(--white)}

/* header */
.brand{left:88px;top:36px;display:flex;align-items:center;gap:12px;font-family:"Open Sans",sans-serif;font-weight:700;font-size:26px;color:var(--pink)}
.brand .dot{width:30px;height:30px;border-radius:50%;background:var(--pink)}
.nav{top:48px;display:flex;font-size:14px;font-weight:700;color:#333;letter-spacing:.3px}
.nav a{position:absolute;white-space:nowrap;color:#333;text-decoration:none}

/* hero */
.hero{left:76px;top:119px;width:1050px;height:538px;background:linear-gradient(160deg,#9aa7ab 0%,#c8b98f 40%,#8a7f6a 70%,#5c574e 100%)}
.hero-title{left:76px;top:303px;width:1050px;text-align:center;font-family:"Oswald",sans-serif;font-weight:600;font-size:70px;color:var(--white);letter-spacing:-1px;line-height:1}
.hero-title span{color:var(--cyan)}
.btn{display:flex;align-items:center;justify-content:center;font-weight:700;color:var(--white);text-transform:uppercase}
.hero-btn{left:515px;top:408px;width:166px;height:50px;background:var(--pink);font-family:"Oswald",sans-serif;font-size:22px;font-weight:500}
.arrow{top:370px;width:30px;height:40px}

/* donation */
.donation{left:76px;top:688px;width:1050px;height:172px;background:var(--cyan)}
.don-title{left:99px;top:730px;font-family:"Oswald",sans-serif;font-weight:500;font-size:31px;color:var(--white)}
.don-btn{left:101px;top:792px;width:130px;height:46px;background:var(--pink);font-family:"Oswald",sans-serif;font-size:20px;font-weight:500}
.don-label{top:713px;font-size:17px;font-weight:700;color:var(--white)}
.don-sub{top:798px;font-size:12px;font-weight:700;color:#1d3c40}
.track{left:368px;top:757px;width:710px;height:16px;border-radius:8px;background:var(--white)}
.fill{left:370px;top:759px;width:285px;height:12px;border-radius:6px;background:var(--green)}
.knob{left:640px;top:750px;width:30px;height:30px;border-radius:50%;background:#222;border:3px solid #555}

/* sections */
.section-title{left:0;width:1200px;text-align:center;font-family:"Oswald",sans-serif;font-weight:500;font-size:31px;color:var(--heading)}
.media{overflow:hidden}
.play{left:50%;top:50%;width:60px;height:42px;margin:-21px 0 0 -30px;border-radius:8px;background:var(--white);display:flex;align-items:center;justify-content:center}

.gps{left:0;top:1237px;width:1200px;height:659px;background:var(--cyan)}
.gps .section-title{color:var(--white)}
.map{left:298px;top:1364px;width:828px;height:481px;border:3px solid #cfd8dc;background:linear-gradient(135deg,#cfe3ec 0%,#e7e2d2 50%,#d6e7ee 100%)}

.entry-h{font-size:26px;font-weight:700;color:var(--pink);line-height:1.25;text-transform:uppercase}
.entry-p{font-size:15px;line-height:23.5px;color:var(--body)}
.read{width:152px;height:48px;background:var(--cyan);font-size:13px}
.divider{left:76px;top:2400px;width:1050px;height:1px;background:var(--rule)}
.band{left:0;top:2822px;width:1200px;height:438px;background:var(--band)}

.card-h{font-size:20px;font-weight:700;color:var(--pink);text-transform:uppercase}
.card-p{font-size:15px;line-height:23px}
.more{font-size:14px;font-weight:700;color:var(--cyan-dark)}

/* join */
.join{left:0;top:3846px;width:1200px;height:144px;background:var(--pink)}
.join-title{left:104px;top:3896px;font-family:"Oswald",sans-serif;font-weight:500;font-size:31px;color:var(--white);letter-spacing:-.5px}
.field{top:3891px;height:57px;background:var(--white);font-size:13px;color:#444;padding-left:12px;display:flex;align-items:center}
.go{left:1024px;top:3891px;width:68px;height:57px;background:var(--cyan);font-size:18px}

/* footer */
.footer{left:0;top:3990px;width:1200px;height:255px;background:var(--footer)}
.foot-brand{left:100px;top:4054px;display:flex;align-items:center;gap:10px;font-weight:700;font-size:22px;color:var(--pink)}
.foot-brand .dot{width:24px;height:24px;border-radius:50%;background:var(--pink)}
.copy{left:99px;top:4150px;font-size:11px;line-height:20px;color:var(--footer-text);text-transform:uppercase}
.foot-h{top:4045px;font-size:14px;font-weight:700;color:var(--cyan);text-transform:uppercase}
.foot-list{top:4072px;list-style:none;font-size:11px;line-height:28px;color:var(--footer-text);text-transform:uppercase}
.social{left:855px;top:4074px;display:flex;gap:6px}
.social span{width:25px;height:25px;border-radius:50%}
</style>
</head>
<body>

<div class="abs backdrop" role="img" aria-label="Blurred roadside photograph behind the top of the page"></div>
<div class="abs column"></div>

<header>
  <div class="abs brand"><span class="dot"></span>Ride the Rim</div>
  <nav class="abs nav">
    <a style="left:606px" href="#">HOME</a>
    <a style="left:693px" href="#">JOURNAL</a>
    <a style="left:806px" href="#">RIDERS</a>
    <a style="left:903px" href="#">SUPPORTERS</a>
    <a style="left:1038px" href="#">CONTACT</a>
  </nav>
</header>

<section>
  <div class="abs hero" role="img" aria-label="Two motorcyclists riding side by side on an open highway, reaching out to each other"></div>
  <h1 class="abs hero-title">RIDE THE RIM <span>2016</span></h1>
  <div class="abs btn hero-btn">Donate Now</div>
  <svg class="abs arrow" style="left:90px" viewBox="0 0 30 40"><path d="M22 4 L6 20 L22 36" fill="none" stroke="#fff" stroke-width="5"/></svg>
  <svg class="abs arrow" style="left:1066px" viewBox="0 0 30 40"><path d="M8 4 L24 20 L8 36" fill="none" stroke="#fff" stroke-width="5"/></svg>
</section>

<section>
  <div class="abs donation"></div>
  <h2 class="abs don-title">DONATION TARGET</h2>
  <div class="abs btn don-btn">Donate</div>
  <div class="abs don-label" style="left:368px">$0</div>
  <div class="abs don-label" style="left:620px">$12,230</div>
  <div class="abs don-label" style="left:1006px">$35,230</div>
  <div class="abs track"></div>
  <div class="abs fill"></div>
  <div class="abs knob"></div>
  <div class="abs don-sub" style="left:368px">NIL</div>
  <div class="abs don-sub" style="left:590px">CURRENT DONATION</div>
  <div class="abs don-sub" style="left:1028px">TARGET</div>
</section>

<section>
  <h2 class="abs section-title" style="top:905px">LIVE VIDEO FEEDS</h2>
  <div class="abs media" style="left:76px;top:982px;width:329px;height:235px;background:linear-gradient(135deg,#c9c4b8,#6e5f50)" role="img" aria-label="Video feed of a rider beside his motorcycle">
    <div class="abs play"><svg width="22" height="24" viewBox="0 0 22 24"><path d="M2 1 L21 12 L2 23Z" fill="#333"/></svg></div>
  </div>
  <div class="abs media" style="left:436px;top:982px;width:328px;height:235px;background:linear-gradient(180deg,#5d8fc9 0%,#9b8e78 50%,#6f7b5e 100%)" role="img" aria-label="Video feed of riders on a road below a carved mountain">
    <div class="abs play"><svg width="22" height="24" viewBox="0 0 22 24"><path d="M2 1 L21 12 L2 23Z" fill="#333"/></svg></div>
  </div>
  <div class="abs media" style="left:795px;top:982px;width:331px;height:235px;background:linear-gradient(135deg,#a07a52,#7a8658 60%,#4f5e3b)" role="img" aria-label="Video feed of motorcycles on a winding canyon road">
    <div class="abs play"><svg width="22" height="24" viewBox="0 0 22 24"><path d="M2 1 L21 12 L2 23Z" fill="#333"/></svg></div>
  </div>
</section>

<section>
  <div class="abs gps"></div>
  <h2 class="abs section-title" style="top:1282px;color:var(--white)">GPS TRACKER</h2>
  <div class="abs map" role="img" aria-label="Map of Australia with the riders' route traced in pink"></div>
</section>

<section>
  <h2 class="abs section-title" style="top:1921px">JOURNAL ENTRIES</h2>

  <div class="abs" style="left:76px;top:2018px;width:510px;height:337px;background:linear-gradient(180deg,#b9bcbf 0%,#6b7563 50%,#5d5d5d 100%)" role="img" aria-label="Two riders on a mountain road lined with pine trees"></div>
  <h3 class="abs entry-h" style="left:625px;top:2014px;width:460px">Two mates. Two bikes. One long road.</h3>
  <p class="abs entry-p" style="left:625px;top:2092px;width:500px">Aliquam molestie, mi et imperdiet euismod, dui purus auctor tellus, et interdum lacus lectus et ante. Sed accumsan sollicitudin sapien, sit amet adipiscing turpis gravida ac. In congue, neque ac lobortis volutpat, libero mauris varius mi, vitae suscipit ipsum ligula vitae risus. Duis aliquam nibh a dui iaculis viverra id a velit.</p>
  <div class="abs btn read" style="left:625px;top:2307px">Read More</div>

  <div class="abs divider"></div>

  <h3 class="abs entry-h" style="left:76px;top:2436px;width:500px">Oh yeah, it's that good. See for yourself.</h3>
  <p class="abs entry-p" style="left:76px;top:2514px;width:500px">Aliquam molestie, mi et imperdiet euismod, dui purus auctor tellus, et interdum lacus lectus et ante. Sed accumsan sollicitudin sapien, sit amet adipiscing turpis gravida ac. In congue, neque ac lobortis volutpat, libero mauris varius mi, vitae suscipit ipsum ligula vitae risus. Duis aliquam nibh a dui iaculis viverra id a velit.</p>
  <div class="abs btn read" style="left:76px;top:2734px">Read More</div>
  <div class="abs" style="left:614px;top:2445px;width:512px;height:337px;background:linear-gradient(135deg,#5a9be0 0%,#3b6fb8 50%,#2a2a2a 100%)" role="img" aria-label="Rider in a helmet beside his motorcycle under a blue sky"></div>

  <div class="abs band"></div>
  <div class="abs" style="left:76px;top:2875px;width:510px;height:334px;background:linear-gradient(135deg,#9aa3ad 0%,#4b7fa6 50%,#2f3f52 100%)" role="img" aria-label="Smiling supporters at a charity run event"></div>
  <h3 class="abs entry-h" style="left:645px;top:2890px;width:480px">What HarbourLight do</h3>
  <p class="abs entry-p" style="left:645px;top:2932px;width:480px">Aliquam molestie, mi et imperdiet euismod, dui purus auctor tellus, et interdum lacus lectus et ante. Sed accumsan sollicitudin sapien, sit amet adipiscing turpis gravida ac. In congue, neque ac lobortis volutpat, libero mauris varius mi, vitae suscipit ipsum ligula vitae risus. Duis aliquam nibh a dui iaculis viverra id a velit.</p>
  <div class="abs btn read" style="left:645px;top:3138px">Read More</div>
</section>

<section>
  <h2 class="abs section-title" style="top:3302px">BLOG POSTS</h2>

  <div class="abs" style="left:76px;top:3382px;width:330px;height:235px;background:linear-gradient(180deg,#b8c6d4 0%,#8b8575 55%,#55524c 100%)" role="img" aria-label="Two riders cruising on a desert highway"></div>
  <h3 class="abs card-h" style="left:76px;top:3640px">Lorem ipsum dolor</h3>
  <p class="abs card-p" style="left:76px;top:3680px;width:330px">Aliquam molestie, mi et imperdiet euismod, dui purus auctor tellus, et interdum lacus lectus et ante.</p>
  <div class="abs more" style="left:76px;top:3780px">Continue Reading</div>

  <div class="abs" style="left:436px;top:3382px;width:329px;height:235px;background:linear-gradient(180deg,#6f94b8 0%,#6a7b5c 50%,#4b4b4b 100%)" role="img" aria-label="Riders on a straight forest road"></div>
  <h3 class="abs card-h" style="left:436px;top:3640px">Lorem ipsum dolor</h3>
  <p class="abs card-p" style="left:436px;top:3680px;width:330px">Aliquam molestie, mi et imperdiet euismod, dui purus auctor tellus, et interdum lacus lectus et ante.</p>
  <div class="abs more" style="left:436px;top:3780px">Continue Reading</div>

  <div class="abs" style="left:795px;top:3382px;width:331px;height:235px;background:linear-gradient(135deg,#8fa860 0%,#5f7f3a 50%,#6e6658 100%)" role="img" aria-label="Motorcyclist leaning into a green hillside bend"></div>
  <h3 class="abs card-h" style="left:795px;top:3640px">Lorem ipsum dolor</h3>
  <p class="abs card-p" style="left:795px;top:3680px;width:330px">Aliquam molestie, mi et imperdiet euismod, dui purus auctor tellus, et interdum lacus lectus et ante.</p>
  <div class="abs more" style="left:795px;top:3780px">Continue Reading</div>
</section>

<section>
  <div class="abs join"></div>
  <h2 class="abs join-title">JOIN US FOR THE RIDE</h2>
  <div class="abs field" style="left:405px;width:300px">Enter Name</div>
  <div class="abs field" style="left:716px;width:297px">Enter Email Address</div>
  <div class="abs btn go">GO</div>
</section>

<footer>
  <div class="abs footer"></div>
  <div class="abs foot-brand"><span class="dot"></span>Ride the Rim</div>
  <p class="abs copy">Copyright © 2016. Company Name.<br>All Right Reserved</p>

  <h4 class="abs foot-h" style="left:408px">Menu Links</h4>
  <ul class="abs foot-list" style="left:408px">
    <li>Home</li><li>Journal</li><li>Riders</li><li>Supporters</li><li>Contact</li>
  </ul>

  <h4 class="abs foot-h" style="left:597px">Recent Posts</h4>
  <ul class="abs foot-list" style="left:597px">
    <li>Duis aliquam nibh</li><li>Dui iaculis viverra id a velit</li><li>Vivamus egestas risus</li><li>Magna varius commodo</li>
  </ul>

  <h4 class="abs foot-h" style="left:855px">Connect Us</h4>
  <div class="abs social">
    <span style="background:#3b6cb5"></span>
    <span style="background:#2ba3d9"></span>
    <span style="background:#777"></span>
    <span style="background:#cf2d3a"></span>
    <span style="background:#dd5a30"></span>
    <span style="background:#d42a2a"></span>
  </div>
</footer>

</body>
</html>
```